Vernac Law Business cards and stationary design project

We are looking for a stationary design for business cards (double sided), 8x10, 5x7, and legal and standard envelopes.

We would like the design to match the logo that we have already.
Color palate preferred is Teal, White, grey and any others that will look good for a professional law firm.

We would like this statement: "RELATIONSHIPS. RESPECT. RESULT" to be on the back of the business cards and maybe on the stationary if it looks good.

Please see link to website for more information: www.vernac-law.example

Target Market(s)

Potential clients that need Attorney services.

Industry/Entity Type

Law Firm

Contact Information for Business Card

We would like the front and back to be two different colors. Current business cards are teal front, grey back and are a vertical design. We are open to options with colors.

Font styles to use
Serif

Colors
33a6d7
33b8a4
b9b9b9
5c5c5c

Requirements
Must have
• Logo supplied needs to go on the card and stationary.
• Match website color palate, www.vernac-law.example
• Be professional and not too wordy.
• Criminal Law, Civil Litigation, Personal Injury, Restraining Orders need to be on the card.
Nice to have
• RELATIONSHIPS. RESPECT. RESULTS. on the back of the card.
Should not have
• Not be too busy/wordy or too flashy.

```html
<!DOCTYPE html>
<html lang="en">
<head>
<meta charset="utf-8">
<title>Vernac Law – Business Card</title>
<link href="https://fonts.googleapis.com/css2?family=Open+Sans:wght@400;600;700&display=swap" rel="stylesheet">
<style>
  :root {
    --teal: #168c9b;
    --teal-light: #1f9aa9;
    --charcoal: #1d1e20;
    --charcoal-soft: #2a2b2e;
    --white: #ffffff;
    --grey-text: #d6d6d6;
    --rule: #4a4b4f;
    --backdrop: #e9e9e9;
  }
  * { box-sizing: border-box; margin: 0; padding: 0; }
  html, body { width: 1200px; height: 844px; overflow: hidden; }
  body {
    background: var(--backdrop);
    font-family: "Open Sans", Arial, sans-serif;
    position: relative;
  }
  .card {
    position: absolute;
    width: 520px;
    height: 298px;
    top: 273px;
    border-radius: 4px;
    overflow: hidden;
    box-shadow: 0 6px 18px rgba(0,0,0,0.18);
  }
  /* Front */
  .card-front {
    left: 50px;
    background: linear-gradient(135deg, var(--charcoal-soft), var(--charcoal));
  }
  .front-brand {
    position: absolute;
    left: 0; top: 0;
    width: 240px; height: 228px;
    display: flex; flex-direction: column;
    align-items: center; justify-content: center;
  }
  .brand-name {
    font-family: "Open Sans", Arial, sans-serif;
    font-weight: 600;
    color: var(--teal-light);
    font-size: 26px;
    white-space: nowrap;
  }
  .brand-mark {
    width: 14px; height: 14px;
    border-radius: 50%;
    background: var(--teal-light);
    margin-bottom: 12px;
  }
  .front-divider {
    position: absolute;
    left: 246px; top: 34px;
    width: 1px; height: 170px;
    background: var(--rule);
  }
  .front-details {
    position: absolute;
    left: 266px; top: 26px;
    color: var(--grey-text);
    font-size: 12.5px;
    line-height: 1.3;
  }
  .person-name {
    color: var(--teal-light);
    font-weight: 700;
    font-size: 17px;
    line-height: 1.1;
  }
  .person-title { margin-bottom: 18px; }
  .address { margin-bottom: 16px; }
  .contact-list { list-style: none; }
  .contact-list li {
    display: flex; align-items: center; gap: 10px;
    height: 19px;
  }
  .contact-list svg { width: 10px; height: 10px; fill: var(--teal-light); flex: none; }
  .practice-band {
    position: absolute;
    left: 0; bottom: 0;
    width: 100%; height: 70px;
    background: var(--teal);
    color: var(--white);
    font-weight: 700;
    font-size: 14px;
    line-height: 1.35;
    text-align: center;
    display: flex; align-items: center; justify-content: center;
    padding: 0 20px;
  }
  /* Back */
  .card-back {
    left: 630px;
    background: var(--teal);
    display: flex; flex-direction: column;
    align-items: center; justify-content: center;
    color: var(--white);
  }
  .card-back .brand-name { color: var(--white); font-size: 32px; }
  .card-back .brand-mark { background: var(--white); width: 16px; height: 16px; }
  .tagline {
    margin-top: 30px;
    font-weight: 700;
    font-size: 13px;
    letter-spacing: 0.3px;
  }
</style>
</head>
<body>
  <section class="card card-front" aria-label="Business card front">
    <div class="front-brand">
      <span class="brand-mark"></span>
      <span class="brand-name">Vernac Law</span>
    </div>
    <div class="front-divider"></div>
    <div class="front-details">
      <p class="person-name">Daniel Marsh</p>
      <p class="person-title">Managing Director</p>
      <p class="address">12345, Address Goes Here<br>Country Name, 123456</p>
      <ul class="contact-list">
        <li><svg viewBox="0 0 10 10"><path d="M2 0.5 L3.6 2.6 L2.8 3.6 Q4 6 6.4 7.2 L7.4 6.4 L9.5 8 L8.4 9.5 Q4 9.5 0.5 1.6 Z"/></svg>(044)-456-7890</li>
        <li><svg viewBox="0 0 10 10"><rect x="2" y="0" width="6" height="10" rx="1"/><rect x="3" y="1.2" width="4" height="6.5" fill="#2a2b2e"/></svg>123-456-7890</li>
        <li><svg viewBox="0 0 10 10"><rect x="0" y="1.5" width="10" height="7"/><path d="M0 1.5 L5 5.5 L10 1.5" stroke="#2a2b2e" stroke-width="1" fill="none"/></svg>info@youremail.com</li>
        <li><svg viewBox="0 0 10 10"><circle cx="5" cy="5" r="5"/><path d="M0 5 H10 M5 0 Q2 5 5 10 M5 0 Q8 5 5 10" stroke="#2a2b2e" stroke-width="0.8" fill="none"/></svg>www.website.com</li>
      </ul>
    </div>
    <div class="practice-band">Practice areas, Criminal Law, Civil Litigation/Personal Injury<br>Restraining Orders</div>
  </section>

  <section class="card card-back" aria-label="Business card back">
    <span class="brand-mark"></span>
    <span class="brand-name">Vernac Law</span>
    <p class="tagline">RELATIONSHIPS. RESPECT. RESULT</p>
  </section>
</body>
</html>
```